Brightmoor Essentials colloidal silver spray for pets.

We need a label for an 8-oz cobalt blue spray bottle. We are a small company just starting to share the benefits of colloidal silver. Our first offering will be the 8-oz spray bottle for pets. We would also like to update our logo. The finished project should be crisp and incorporate a dog on the label. I have attached the information we would like on the label and our logo, which can be changed to match your vision.
Updates

Hi, I would like to remind you that we are using a cobalt blue bottle with a black sprayer and would like an updated logo. Also, for the business cards, we don't want an animal on them, as we are planning future products for people. thank you

```html
<!DOCTYPE html>
<html lang="en">
<head>
<meta charset="utf-8">
<title>Brightmoor Essentials – Colloidal Silver Label</title>
<link href="https://fonts.googleapis.com/css2?family=Rye&family=Nunito:wght@800;900&family=Signika:wght@400;600&display=swap" rel="stylesheet">
<style>
  :root{
    --page:#e9e9ea;
    --label-top:#e2e4f4;
    --label-mid:#a3aad9;
    --label-bottom:#5663b4;
    --title-green:#179a4c;
    --title-shade:#0b5a2c;
    --band:#2e3190;
    --white:#ffffff;
    --navy:#262a7a;
    --suds-light:#eaf8fb;
    --suds:#a8dde8;
    --red:#e2262b;
    --brand-ink:#2e3190;
  }
  *{box-sizing:border-box;margin:0;padding:0}
  html,body{width:1200px;height:1200px;overflow:hidden;background:var(--page)}
  .canvas{position:relative;width:1200px;height:1200px;background:radial-gradient(circle at 50% 45%,#f6f6f7 0%,var(--page) 70%)}

  .brand-lockup{position:absolute;left:730px;top:185px;display:flex;align-items:center;gap:14px;white-space:nowrap}
  .brand-lockup .dot{width:20px;height:20px;border-radius:50%;background:var(--brand-ink);flex:none}
  .brand-lockup .name{font-family:"Signika",sans-serif;font-weight:600;font-size:36px;color:var(--brand-ink);line-height:1.1}

  .label{position:absolute;left:140px;top:50px;width:525px;height:1100px;overflow:hidden;
    background:linear-gradient(180deg,var(--label-top) 0%,var(--label-mid) 45%,var(--label-bottom) 100%);
    box-shadow:0 6px 24px rgba(0,0,0,.12)}

  .label-brand{position:absolute;top:60px;left:0;right:0;display:flex;justify-content:center;align-items:center;gap:8px}
  .label-brand .dot{width:10px;height:10px;border-radius:50%;background:var(--brand-ink)}
  .label-brand .name{font-family:"Signika",sans-serif;font-weight:600;font-size:18px;color:var(--brand-ink)}

  .product-title{position:absolute;top:130px;left:0;right:0;text-align:center;font-family:"Rye",serif;
    color:var(--title-green);line-height:1;font-weight:400;
    text-shadow:2px 2px 0 var(--white),4px 4px 0 var(--title-shade)}
  .product-title span{display:block;white-space:nowrap;transform:scaleX(.64);transform-origin:50% 50%;
    margin-left:-120px;margin-right:-120px;font-size:110px}
  .product-title .line-2{margin-top:4px}

  .claim-band{position:absolute;top:372px;left:57px;width:412px;height:94px;border-radius:20px;background:var(--band);
    display:flex;flex-direction:column;justify-content:center;align-items:center;
    font-family:"Nunito",sans-serif;font-weight:900;font-size:34px;color:var(--white);letter-spacing:1px;line-height:1.15}

  .specs{position:absolute;top:478px;left:0;right:0;text-align:center;font-family:"Signika",sans-serif;font-weight:600;font-size:23px;color:var(--white);line-height:1.25}
  .specs-rule{display:block;width:310px;height:2px;background:var(--white);margin:4px auto 0}

  .benefits{position:absolute;top:562px;left:0;right:0;text-align:center;font-family:"Signika",sans-serif;font-weight:600;font-size:20.5px;color:var(--white);line-height:1.25}

  .dog-art{position:absolute;left:0;top:720px;width:525px;height:380px;
    background:radial-gradient(ellipse at 50% 32%,#e9773f 0%,#f0a36e 24%,rgba(168,221,232,.9) 46%,var(--suds-light) 100%)}

  .for-dogs{position:absolute;left:392px;top:746px;width:122px;height:100px;border-radius:50px;background:var(--suds-light);
    display:flex;flex-direction:column;justify-content:center;align-items:center;
    font-family:"Nunito",sans-serif;font-weight:900;font-size:24px;color:var(--navy);line-height:1.05}

  .origin{position:absolute;left:52px;top:1027px;display:flex;align-items:center;gap:8px}
  .origin .flag{display:block}
  .origin .divider{width:2px;height:32px;background:var(--red)}
  .origin .text{font-family:"Signika",sans-serif;font-size:15.5px;color:var(--red);line-height:1.05}

  .volume{position:absolute;right:52px;top:1032px;font-family:"Signika",sans-serif;font-weight:600;font-size:20px;color:var(--navy)}
</style>
</head>
<body>
<main class="canvas">

  <section class="label" aria-label="Spray bottle label">
    <div class="label-brand"><span class="dot"></span><span class="name">Brightmoor Essentials</span></div>

    <h1 class="product-title"><span class="line-1">COLLOIDAL</span><span class="line-2">SILVER</span></h1>

    <div class="claim-band"><span>NATURAL FIRST AID</span><span>FOR PETS</span></div>

    <p class="specs">10 PPM - No Preservaties<br>100% Pure - No Additives<span class="specs-rule"></span></p>

    <p class="benefits">Anti microbial, Anti Fungal,<br>Anti Bacterial, Anti Viral<br>Treats burns, Bites, Cuts, Abrasions,<br>Hots Spots</p>

    <div class="dog-art" role="img" aria-label="Illustration of a smiling orange dog in a pile of soap bubbles"></div>

    <div class="for-dogs"><span>FOR</span><span>DOGS</span></div>

    <div class="origin">
      <svg class="flag" width="68" height="32" viewBox="0 0 68 32" aria-hidden="true">
        <rect width="17" height="32" fill="#e2262b"/>
        <rect x="17" width="34" height="32" fill="#ffffff"/>
        <rect x="51" width="17" height="32" fill="#e2262b"/>
      </svg>
      <span class="divider"></span>
      <span class="text">MADE IN<br>CANADA</span>
    </div>
    <div class="volume">8 oz / 250 ml</div>
  </section>

  <div class="brand-lockup"><span class="dot"></span><span class="name">Brightmoor Essentials</span></div>

</main>
</body>
</html>
```